Norrell Advisory WA Business Card

Create an interesting, eye catching and colourful two sided business card. We are a business consulting operation assisting SME's improve all areas of their business. We provide consulting services to assist SME's to create a culture of continuous improvement, making a positive difference in the business. Our tag line is Small changes, big rewards. We want to create a well recognised, innovative brand that can be continued throughout our website, social media and email correspondence.

Target Market(s)

Small to Medium Enterprise Business Owners

Industry/Entity Type

Business Consultant

Contact Information for Business Card

Name of Business: Norrell Advisory - Small Changes Big Rewards
Derek Holloway Ph 0407385510 Megan Holloway Ph 0407913847
Email norrelladvisorywa@mailbox-example.com
Web address TBA
FaceBook page TBA

BACKSIDE OF CARD

Providing assistance with:

• Organisation & Efficiency
• Revenue generation & Marketing
• Financial Management
• Production quality & delivery
• Systems & Process documentation
• Exit Strategy

Font styles to use
Other font styles liked:
• Calibri

Colors

Designer to choose colors to be used in the design.

Requirements
Must have
• Calibri font

```html
<!DOCTYPE html>
<html lang="en">
<head>
<meta charset="utf-8">
<title>Norrell Advisory WA Business Card</title>
<link rel="stylesheet" href="https://fonts.googleapis.com/css2?family=Carlito:wght@400;700&display=swap">
<style>
  :root {
    --page-bg: #cfcfcf;
    --card-white: #ffffff;
    --card-dark: #2c2c2c;
    --ink-dark: #222222;
    --ink-light: #f2f2f2;
    --accent-blue: #2f8fd0;
    --accent-red: #e8402f;
    --accent-green: #8cc63f;
    --accent-yellow: #f7d928;
    --divider: #555555;
  }
  * { box-sizing: border-box; margin: 0; padding: 0; }
  html, body {
    width: 1200px; height: 802px; overflow: hidden;
    background: var(--page-bg);
    font-family: "Carlito", "Calibri", sans-serif;
  }
  .stage { position: relative; width: 1200px; height: 802px; }
  .card {
    position: absolute; top: 274px;
    width: 443px; height: 265px; overflow: hidden;
  }
  .card-front { left: 136px; background: var(--card-white); color: var(--ink-dark); }
  .card-back { left: 624px; background: var(--card-dark); color: var(--ink-light); }

  /* front */
  .front-decoration { position: absolute; left: 0; top: 0; width: 230px; height: 265px; }
  .contact-block { position: absolute; right: 23px; top: 52px; text-align: right; }
  .person { margin-bottom: 12px; }
  .person-name { font-size: 19px; font-weight: 700; text-transform: uppercase; letter-spacing: 0.2px; line-height: 21px; }
  .person-phone { font-size: 12px; line-height: 14px; display: flex; justify-content: flex-end; align-items: center; gap: 4px; }
  .links { position: absolute; right: 22px; top: 174px; text-align: right; }
  .link-row { font-size: 12.5px; line-height: 18px; display: flex; justify-content: flex-end; align-items: center; gap: 5px; }
  .icon { width: 10px; height: 10px; flex: none; }

  /* back */
  .brand { position: absolute; left: 0; top: 60px; width: 214px; text-align: center; }
  .brand-mark { width: 34px; height: 34px; border-radius: 50%; background: var(--accent-red); margin: 0 auto 62px; }
  .brand-name { font-size: 19px; font-weight: 700; text-transform: uppercase; letter-spacing: 0.3px; }
  .back-divider { position: absolute; left: 214px; top: 75px; width: 1px; height: 118px; background: var(--divider); }
  .services { position: absolute; left: 226px; top: 69px; }
  .services-title { font-size: 12px; font-weight: 700; text-transform: uppercase; margin-bottom: 11px; }
  .services-list { list-style: none; font-size: 12.6px; line-height: 15.8px; }
  .services-list li::before { content: "•"; margin-right: 3px; font-size: 9px; vertical-align: 1px; }
  .tagline { position: absolute; left: 0; right: 0; top: 224px; text-align: center; font-size: 13px; text-transform: uppercase; }
</style>
</head>
<body>
<div class="stage">

  <section class="card card-front">
    <svg class="front-decoration" role="img" aria-label="Colourful abstract decoration in blue, red, green and yellow" viewBox="0 0 230 265">
      <defs>
        <linearGradient id="decoration-fill" x1="0" y1="0" x2="1" y2="1">
          <stop offset="0" stop-color="var(--accent-blue)"/>
          <stop offset="0.35" stop-color="var(--accent-yellow)"/>
          <stop offset="0.55" stop-color="var(--accent-red)"/>
          <stop offset="1" stop-color="var(--accent-green)"/>
        </linearGradient>
      </defs>
      <path d="M0 0 H125 C160 60 230 110 220 150 C210 200 140 220 110 265 H0 Z" fill="url(#decoration-fill)"/>
    </svg>

    <div class="contact-block">
      <div class="person">
        <div class="person-name">Derek Holloway</div>
        <div class="person-phone">0407385510
          <svg class="icon" viewBox="0 0 10 10"><path d="M2 0.5 L3.6 2.4 L2.8 3.6 C3.4 5 4.6 6.4 6 7 L7.2 6.2 L9 7.8 L7.8 9.5 C4 9 1 5.5 0.6 1.8 Z" fill="var(--accent-blue)"/></svg>
        </div>
      </div>
      <div class="person">
        <div class="person-name">Megan Holloway</div>
        <div class="person-phone">0407913847
          <svg class="icon" viewBox="0 0 10 10"><path d="M2 0.5 L3.6 2.4 L2.8 3.6 C3.4 5 4.6 6.4 6 7 L7.2 6.2 L9 7.8 L7.8 9.5 C4 9 1 5.5 0.6 1.8 Z" fill="var(--accent-blue)"/></svg>
        </div>
      </div>
    </div>

    <div class="links">
      <div class="link-row">norrelladvisorywa@mailbox-example.com
        <svg class="icon" viewBox="0 0 10 10"><rect x="0.5" y="2" width="9" height="6.5" fill="var(--accent-blue)"/><path d="M0.5 2 L5 5.6 L9.5 2" fill="none" stroke="#fff" stroke-width="0.8"/></svg>
      </div>
      <div class="link-row">www.norrelladvisory-example.com
        <svg class="icon" viewBox="0 0 10 10"><circle cx="5" cy="5" r="5" fill="var(--accent-blue)"/></svg>
      </div>
      <div class="link-row">social-example.com/norrelladvisory
        <svg class="icon" viewBox="0 0 10 10"><circle cx="5" cy="5" r="5" fill="var(--accent-blue)"/></svg>
      </div>
    </div>
  </section>

  <section class="card card-back">
    <div class="brand">
      <div class="brand-mark"></div>
      <div class="brand-name">Norrell Advisory</div>
    </div>
    <div class="back-divider"></div>
    <div class="services">
      <h2 class="services-title">Providing assistance with:</h2>
      <ul class="services-list">
        <li>Organisation &amp; Efficiency</li>
        <li>Revenue generation &amp; Marketing</li>
        <li>Financial Management</li>
        <li>Production quality &amp; delivery</li>
        <li>Systems &amp; Process documentation</li>
        <li>Exit Strategy</li>
      </ul>
    </div>
    <p class="tagline">Small changes big rewards</p>
  </section>

</div>
</body>
</html>
```